Business Cards for Volmont Hayes, a law firm

We changed our firm's name from "Volmont & Hayes LLP" to "Volmont Hayes", we need to update our cards with a new design. We like the overall look of the back but the front side of the cards (see attached mockup) needs a refreshed look. I also attach our current logo so you can get rid of that LLP and &. We have a new address as well (not same as on mockup).

Target Market(s)

Clients of law firm

Industry/Entity Type

Law Firm

Contact Information for Business Card

Frontsides:

Lorenzo T. Volmont
Partner
Tel: (416) 555-0172 ext. 101
Fax: (647) 555-0139
Email: lvolmont@vhlegal.example

Simon P. Hayes
Partner
Tel: (416) 555-0172 ext. 102
Fax: (647) 555-0139
Email: simonhayes@vhlegal.example

Mark E. Dorsan
Barrister
Tel: (416) 555-0172 ext. 104
Fax: (647) 555-0139
Email: mdorsan@vhlegal.example

The back side should be crimson red (see mockup) with the logo (please update it to remove the & and the LLP, you can modify it a bit to make it tasteful if need be). Our new address is

82 Marlow Rd W, Suite 710
Toronto, ON M5K 0Z9

After our address, please also include our website www.vhlegal.example

Font styles to use
Sans Serif

Colors
ec2027
ffffff
000000

Requirements
Must have
• PLEASE NOTE: our firm's colour is more of a darker/crimson red, not a vibrant red.
• The front should have space for the lawyer's name, title, phone number (with extension), fax number, and email.
• If you're going to add those yourself, the info for the frontside is in the "Business Card Details" section (three lawyers that need their own cards).
Nice to have
• We like the backside of our current cards, just update it with our new address (one address now instead of 2), and a slightly modified logo (not a new logo altogether).
• The frontside should be refreshed with a better look (think minimalist, professional and modern), although still predominantly white-based background.
Should not have
• No scales of justice or other cheesy lawyer stereotype symbols! :-)

```html
<!DOCTYPE html>
<html lang="en">
<head>
<meta charset="utf-8">
<title>Volmont Hayes – Business Card Concepts</title>
<link href="https://fonts.googleapis.com/css2?family=Barlow:wght@400;500;600;700&display=swap" rel="stylesheet">
<style>
  :root {
    --sheet: #f2f2f2;
    --crimson: #c11f18;
    --red: #e1403c;
    --ink: #111111;
    --charcoal: #333333;
    --band-dark: #2a2a2a;
    --white: #ffffff;
    --accent: #d9302b;
    --muted: #d0d0d0;
    --ghost: #f1f1f1;
    --text: #222222;
  }
  * { box-sizing: border-box; margin: 0; padding: 0; }
  html, body { width: 1156px; height: 1200px; overflow: hidden; }
  body {
    background: var(--sheet);
    font-family: "Barlow", "Helvetica Neue", Arial, sans-serif;
    color: var(--text);
    position: relative;
  }
  .icons { position: absolute; width: 0; height: 0; }

  .card {
    position: absolute;
    width: 524px;
    height: 262px;
    overflow: hidden;
    background: var(--white);
    box-shadow: 0 1px 4px rgba(0,0,0,.14);
  }
  .card--crimson { background: var(--crimson); color: var(--white); }
  .card--red { background: var(--red); color: var(--white); }
  .card--charcoal { background: var(--charcoal); color: var(--white); }

  .pos-1 { left: 53px;  top: 38px; }
  .pos-2 { left: 606px; top: 38px; }
  .pos-3 { left: 49px;  top: 324px; }
  .pos-4 { left: 606px; top: 324px; }
  .pos-5 { left: 48px;  top: 616px; }
  .pos-6 { left: 603px; top: 616px; }
  .pos-7 { left: 48px;  top: 901px; }
  .pos-8 { left: 592px; top: 901px; }

  /* wordmark */
  .wordmark { display: flex; align-items: center; gap: 9px; font-weight: 700; white-space: nowrap; letter-spacing: .2px; }
  .wordmark .dot { border-radius: 50%; flex: none; }
  .wordmark--lg { font-size: 31px; }
  .wordmark--lg .dot { width: 22px; height: 22px; }
  .wordmark--sm { font-size: 19px; }
  .wordmark--sm .dot { width: 14px; height: 14px; }
  .wordmark--white { color: var(--white); }
  .wordmark--white .dot { background: var(--white); }
  .wordmark--white-red .dot { background: var(--red); }
  .wordmark--ink { color: var(--ink); }
  .wordmark--ink .dot { background: var(--accent); }
  .wordmark--accent { color: var(--accent); }
  .wordmark--accent .dot { background: var(--ink); }

  /* back side */
  .back-logo { position: absolute; left: 0; right: 0; top: 122px; display: flex; justify-content: center; }
  .back-band {
    position: absolute; left: 0; right: 0; bottom: 0; height: 72px;
    border-top: 1.5px solid rgba(0,0,0,.75);
    display: flex; align-items: center; justify-content: space-between;
    padding: 0 44px 0 22px;
  }
  .card--white .back-band { border-top: 3px solid var(--muted); }
  .card--charcoal .back-band { background: var(--band-dark); }
  .address { display: flex; align-items: flex-start; gap: 8px; font-size: 12.5px; font-weight: 600; line-height: 1.25; }
  .address svg { width: 12px; height: 16px; flex: none; margin-top: 1px; }
  .website { font-size: 12.5px; font-weight: 700; letter-spacing: .3px; }
  .card--white .website { color: var(--accent); }
  .card--white .address { color: var(--text); }

  /* front side */
  .person-name { font-size: 16px; font-weight: 700; letter-spacing: .6px; color: var(--ink); }
  .person-name--accent { color: var(--accent); }
  .person-title { font-size: 12.5px; color: var(--accent); margin-top: 2px; }
  .contacts { list-style: none; font-size: 13.5px; line-height: 1.17; color: var(--text); letter-spacing: .2px; }
  .contacts li { display: flex; align-items: center; gap: 7px; }
  .contacts svg { width: 10px; height: 10px; fill: var(--accent); flex: none; }

  .split-logo { position: absolute; left: 52px; }
  .split-rule { position: absolute; top: 40px; bottom: 38px; width: 3px; background: var(--ghost); }
  .split-info { position: absolute; }
  .split-info .contacts { margin-top: 20px; }

  .stack-logo { position: absolute; right: 38px; top: 84px; }
  .stack-info { position: absolute; left: 30px; top: 103px; }
  .stack-rule { width: 180px; height: 3px; background: var(--ghost); margin: 22px 0; }

  .row-info { position: absolute; left: 30px; top: 145px; }
  .row-band {
    position: absolute; left: 0; right: 0; bottom: 0; height: 66px;
    border-top: 2px solid var(--muted);
    display: flex; justify-content: space-between; padding: 22px 52px 0 30px;
    font-size: 13px; line-height: 1.2;
  }
  .row-band b { font-weight: 700; }
</style>
</head>
<body>

<svg class="icons" aria-hidden="true">
  <defs>
    <symbol id="icon-pin" viewBox="0 0 12 16"><path d="M6 0a6 6 0 0 0-6 6c0 4.5 6 10 6 10s6-5.5 6-10a6 6 0 0 0-6-6zm0 8.3A2.3 2.3 0 1 1 6 3.7a2.3 2.3 0 0 1 0 4.6z"/></symbol>
    <symbol id="icon-phone" viewBox="0 0 10 10"><path d="M2 .3l1.6 1.9-.9 1.3a6 6 0 0 0 3.8 3.8l1.3-.9L9.7 8 8.6 9.7C4.4 9.6.4 5.6.3 1.4z"/></symbol>
    <symbol id="icon-fax" viewBox="0 0 10 10"><path d="M2.5 0h5v3h-5zM0 3.5h10v4.5H8V6H2v2H0zM2.5 6.5h5V10h-5z"/></symbol>
    <symbol id="icon-mail" viewBox="0 0 10 10"><path d="M0 2h10v6H0zm1 1v.4l4 2.4 4-2.4V3z"/></symbol>
  </defs>
</svg>

<section class="card card--crimson pos-1">
  <div class="back-logo"><div class="wordmark wordmark--lg wordmark--white"><span class="dot"></span>Volmont Hayes</div></div>
  <div class="back-band">
    <div class="address"><svg fill="#111"><use href="#icon-pin"/></svg><span>82 Marlow Rd W, Suite 710<br>Toronto, ON M5K 0Z9</span></div>
    <div class="website">www.vhlegal.example</div>
  </div>
</section>

<section class="card pos-2">
  <div class="split-logo" style="top:152px;"><div class="wordmark wordmark--sm wordmark--accent"><span class="dot"></span>Volmont Hayes</div></div>
  <div class="split-rule" style="left:221px;"></div>
  <div class="split-info" style="left:278px; top:88px;">
    <div class="person-name">Lorenzo T. Volmont</div>
    <div class="person-title">Partner</div>
    <ul class="contacts">
      <li><svg><use href="#icon-phone"/></svg>(416) 555-0172 ext. 101</li>
      <li><svg><use href="#icon-fax"/></svg>(647) 555-0139</li>
      <li><svg><use href="#icon-mail"/></svg>lvolmont@vhlegal.example</li>
    </ul>
  </div>
</section>

<section class="card pos-3">
  <div class="stack-logo"><div class="wordmark wordmark--sm wordmark--accent"><span class="dot"></span>Volmont Hayes</div></div>
  <div class="stack-info">
    <div class="person-name person-name--accent">Lorenzo T. Volmont</div>
    <div class="person-title">Partner</div>
    <div class="stack-rule"></div>
    <ul class="contacts">
      <li><svg><use href="#icon-phone"/></svg>(416) 555-0172 ext. 101</li>
      <li><svg><use href="#icon-fax"/></svg>(647) 555-0139</li>
      <li><svg><use href="#icon-mail"/></svg>lvolmont@vhlegal.example</li>
    </ul>
  </div>
</section>

<section class="card pos-4">
  <div class="split-logo" style="top:152px;"><div class="wordmark wordmark--sm wordmark--accent"><span class="dot"></span>Volmont Hayes</div></div>
  <div class="split-rule" style="left:234px;"></div>
  <div class="split-info" style="left:292px; top:90px;">
    <div class="person-name">Lorenzo T. Volmont</div>
    <div class="person-title">Partner</div>
    <ul class="contacts">
      <li><svg><use href="#icon-phone"/></svg>(416) 555-0172 ext. 101</li>
      <li><svg><use href="#icon-fax"/></svg>(647) 555-0139</li>
      <li><svg><use href="#icon-mail"/></svg>lvolmont@vhlegal.example</li>
    </ul>
  </div>
</section>

<section class="card card--red pos-5">
  <div class="back-logo"><div class="wordmark wordmark--lg wordmark--white"><span class="dot"></span>Volmont Hayes</div></div>
  <div class="back-band">
    <div class="address"><svg fill="#111"><use href="#icon-pin"/></svg><span>82 Marlow Rd W, Suite 710<br>Toronto, ON M5K 0Z9</span></div>
    <div class="website">www.vhlegal.example</div>
  </div>
</section>

<section class="card card--white pos-6">
  <div class="back-logo"><div class="wordmark wordmark--lg wordmark--ink"><span class="dot"></span>Volmont Hayes</div></div>
  <div class="back-band">
    <div class="address"><svg fill="#d9302b"><use href="#icon-pin"/></svg><span>82 Marlow Rd W, Suite 710<br>Toronto, ON M5K 0Z9</span></div>
    <div class="website">www.vhlegal.example</div>
  </div>
</section>

<section class="card card--charcoal pos-7">
  <div class="back-logo"><div class="wordmark wordmark--lg wordmark--white wordmark--white-red"><span class="dot"></span>Volmont Hayes</div></div>
  <div class="back-band">
    <div class="address"><svg fill="#e1403c"><use href="#icon-pin"/></svg><span>82 Marlow Rd W, Suite 710<br>Toronto, ON M5K 0Z9</span></div>
    <div class="website">www.vhlegal.example</div>
  </div>
</section>

<section class="card pos-8">
  <div class="stack-logo"><div class="wordmark wordmark--sm wordmark--accent"><span class="dot"></span>Volmont Hayes</div></div>
  <div class="row-info">
    <div class="person-name person-name--accent">Lorenzo T. Volmont</div>
    <div class="person-title">Partner</div>
  </div>
  <div class="row-band">
    <div><b>Tel:</b> (416) 555-0172 ext. 101<br><b>Fax:</b> (647) 555-0139</div>
    <div><b>Email:</b> lvolmont@vhlegal.example</div>
  </div>
</section>

</body>
</html>
```